VELORA Brisbane Tiling Service

My name is Milos Brendt i need a business card for a new company. We are wall and floor tilers based in Brisbane, our company is Velorix Brisbane Tiling Service.
We would like a logo from our website used on our cards. Our website is www.velorix.com.au

I would like my Chatterbook and Postwave accounts on my card.

Industry/Entity Type

Business

Colors
0692cd
3176b5
33a6d7
85cae6

```html
<!DOCTYPE html>
<html lang="en">
<head>
<meta charset="utf-8">
<title>Velorix Brisbane Tiling Service – Business Cards</title>
<link href="https://fonts.googleapis.com/css2?family=Lato:wght@400;700&display=swap" rel="stylesheet">
<style>
  :root{
    --stage:#2a2a2a;
    --card:#f4f4f4;
    --card-shade:#e4e4e4;
    --blue:#0692cd;
    --blue-deep:#3176b5;
    --blue-mid:#33a6d7;
    --blue-light:#85cae6;
    --ink:#3a3a3a;
    --ink-soft:#555;
    --edge:#5a5a5a;
  }
  *{box-sizing:border-box;margin:0;padding:0}
  html,body{width:1200px;height:997px;overflow:hidden}
  body{background:var(--stage);font-family:"Lato",sans-serif;position:relative}

  .card{
    position:absolute;width:570px;height:326px;overflow:hidden;
    background:linear-gradient(135deg,var(--card) 0%,#fafafa 45%,var(--card-shade) 100%);
    box-shadow:0 18px 40px rgba(0,0,0,.55);
  }
  .card--front{left:70px;top:80px}
  .card--back{left:560px;top:560px}

  .card__texture{position:absolute;inset:0}

  .brand{position:absolute;display:flex;align-items:center;gap:14px}
  .brand__square{width:78px;height:78px;background:var(--blue)}
  .brand__name{font-size:54px;font-weight:400;color:var(--blue);line-height:.9;letter-spacing:.5px}
  .brand__tagline{font-size:22px;color:var(--ink);line-height:1.1;margin-top:4px}
  .card--front .brand{left:110px;top:96px}
  .card--back .brand{left:150px;top:48px}
  .card--back .brand__square{width:64px;height:64px}
  .card--back .brand__name{font-size:44px}
  .card--back .brand__tagline{font-size:18px}

  .website{
    position:absolute;left:0;right:0;top:212px;text-align:center;
    font-size:15px;font-weight:700;letter-spacing:4px;color:var(--ink);
  }

  .band{position:absolute;left:0;bottom:0;width:100%;height:70px}

  .holder{position:absolute;right:70px;top:128px;text-align:left}
  .holder__name{font-size:20px;font-weight:700;color:var(--blue-deep);padding:0 6px 2px;border-bottom:2px solid var(--blue-deep)}
  .holder__phone{font-size:19px;color:var(--ink);padding:2px 18px 0}

  .contact-tab{position:absolute;left:0;top:182px;width:38px;height:120px;background:var(--blue);border-radius:0 10px 10px 0}
  .contact-tab svg{display:block;margin:10px auto 0}
  .contact-list{position:absolute;left:52px;top:184px;list-style:none}
  .contact-list li{font-size:13px;color:var(--ink-soft);height:28px;line-height:28px}
</style>
</head>
<body>

<section class="card card--front" aria-label="Card front">
  <div class="card__texture" role="img" aria-label="Soft grey tiled checker background"></div>
  <div class="brand">
    <div class="brand__square"></div>
    <div>
      <div class="brand__name">velorix</div>
      <div class="brand__tagline">brisbane tiling service</div>
    </div>
  </div>
  <p class="website">www.velorix.com.au</p>
  <svg class="band" viewBox="0 0 570 70" preserveAspectRatio="none">
    <path d="M330 70 Q330 56 352 52 L570 8 L570 70 Z" fill="var(--blue)"/>
    <path d="M345 70 Q345 62 362 60 L570 22 L570 70 Z" fill="#fff" opacity=".0"/>
  </svg>
</section>

<section class="card card--back" aria-label="Card back">
  <div class="card__texture" role="img" aria-label="Soft grey tiled checker background"></div>
  <div class="brand">
    <div class="brand__square"></div>
    <div>
      <div class="brand__name">velorix</div>
      <div class="brand__tagline">brisbane tiling service</div>
    </div>
  </div>

  <div class="holder">
    <div class="holder__name">Milos Brendt</div>
    <div class="holder__phone">0412608317</div>
  </div>

  <div class="contact-tab">
    <svg width="14" height="18" viewBox="0 0 14 18"><rect x="2" y="1" width="10" height="16" rx="2" fill="none" stroke="#fff" stroke-width="1.6"/></svg>
    <svg width="18" height="14" viewBox="0 0 18 14"><rect x="1" y="1" width="16" height="12" fill="none" stroke="#fff" stroke-width="1.6"/><path d="M1 1 L9 8 L17 1" fill="none" stroke="#fff" stroke-width="1.6"/></svg>
    <svg width="14" height="14" viewBox="0 0 14 14"><circle cx="7" cy="7" r="6" fill="#fff"/></svg>
    <svg width="14" height="14" viewBox="0 0 14 14"><circle cx="7" cy="7" r="6" fill="#fff"/></svg>
  </div>
  <ul class="contact-list">
    <li>07 3155 0294</li>
    <li>info@velorix.com.au</li>
    <li>Postwave/ InfoVelorix</li>
    <li>Chatterbook/Velorix - Brisbane Tiling Service</li>
  </ul>

  <svg class="band" viewBox="0 0 570 70" preserveAspectRatio="none">
    <rect x="0" y="52" width="570" height="18" fill="var(--edge)"/>
    <path d="M360 56 Q362 40 385 36 L570 2 L570 56 Z" fill="var(--blue)"/>
  </svg>
</section>

</body>
</html>
```